Custom PowerPoint Template for Training & Workshop Presentations

I am looking for a professional designer to create a custom PowerPoint template (PPTX) for my training and workshop materials. My trainings are designed for: HR professionals and Learning & Development specialists;
Executives and team leaders; Organizations investing in employee development and workplace learning; Participants in professional development workshops, seminars, and didactics trainings
The template should therefore appear trustworthy, calm, friendly, structured, and competence‑oriented. The design should be visually appealing, easy to read, and fully editable.

All branding files are attached to this project.
Please use them as the main reference for your design:
Logo (included as attachment)
Brand color specifications (included as attachment)
Font specifications related to the logo and brand (included as attachment)

What I need:
--> Title Slide: Title, subtitle, name, logo
(1–2 variations)
--> Agenda / Overview Slide
--> Content Slides
--> Text only
--> Text + image
-->Two-column
--> Section header
--> Quote / key message
--> Graphic / Model Slides: (1–2 layouts for frameworks, processes, models)
--> Tables & Charts: (Table styles in brand colors; Chart design aligned with typography and color palette)
--> Closing Slide: (Contact or call-to-action; Optional second variation)

All layouts must be built properly inside the PowerPoint Slide Master

```html
<!DOCTYPE html>
<html lang="de">
<head>
<meta charset="utf-8">
<title>Gemeinsam Kompetenzen entwickeln – Folienvorlage</title>
<link rel="stylesheet" href="https://fonts.googleapis.com/css2?family=Roboto:wght@500;700&family=Quicksand:wght@400;500&display=swap">
<style>
  :root {
    --stage: #4a5058;
    --paper: #ffffff;
    --brand-dark: #1a5e91;
    --brand-light: #8eabc4;
    --ink: #3a3a3a;
    --ink-strong: #222222;
  }
  * { margin: 0; padding: 0; box-sizing: border-box; }
  html, body { width: 1200px; height: 1001px; overflow: hidden; }
  body { background: var(--stage); position: relative; font-family: "Quicksand", sans-serif; color: var(--ink); }

  .slide { position: absolute; left: 242px; width: 716px; background: var(--paper); overflow: hidden; }
  .slide--overview { top: 70px; height: 402px; }
  .slide--model { top: 526px; height: 403px; }

  .slide-title { position: absolute; font-family: "Roboto", sans-serif; font-weight: 500; font-size: 17px; line-height: 20px; white-space: nowrap; }
  .slide-title .lead { color: var(--brand-light); display: block; }
  .slide-title .main { color: var(--brand-dark); display: block; font-weight: 700; }
  .slide-title::after { content: ""; position: absolute; left: 0; top: 46px; width: 29px; height: 2.5px; background: var(--brand-dark); }
  .slide--overview .slide-title { left: 42px; top: 28px; }
  .slide--model .slide-title { left: 51px; top: 45px; }

  .point { position: absolute; width: 300px; height: 48px; }
  .point-number { position: absolute; left: 0; top: 0; width: 48px; height: 48px; color: #fff; font-size: 19px; display: flex; align-items: center; justify-content: center; font-weight: 400; }
  .point-number--dark { background: var(--brand-dark); }
  .point-number--light { background: var(--brand-light); }
  .point-text { position: absolute; left: 65px; top: 0; font-size: 9px; line-height: 16px; color: var(--ink); white-space: nowrap; }
  .point--1 { left: 42px; top: 120px; }
  .point--2 { left: 392px; top: 120px; }
  .point--3 { left: 42px; top: 185px; }
  .point--4 { left: 392px; top: 185px; }

  .summary-heading { position: absolute; left: 0; width: 100%; top: 284px; text-align: center; font-family: "Roboto", sans-serif; font-weight: 700; font-size: 17px; line-height: 20px; color: var(--brand-dark); }
  .summary-text { position: absolute; left: 0; width: 100%; top: 311px; text-align: center; font-size: 9px; line-height: 16px; color: var(--ink); white-space: nowrap; }

  .block { position: absolute; width: 150px; }
  .block-title { font-size: 14.4px; color: var(--ink-strong); font-weight: 400; margin-bottom: 6px; line-height: 18px; white-space: nowrap; }
  .block-text { font-size: 9px; line-height: 16px; color: var(--ink); white-space: nowrap; }
  .block--left { left: 70px; text-align: right; }
  .block--right { left: 497px; text-align: left; }
  .block--top { top: 114px; }
  .block--bottom { top: 269px; }

  .model-graphic { position: absolute; left: 230px; top: 124px; width: 258px; height: 205px; }
</style>
</head>
<body>

  <section class="slide slide--overview">
    <h1 class="slide-title"><span class="lead">GEMEINSAM KOMPETENZEN</span><span class="main">ENTWICKELN</span></h1>

    <div class="point point--1">
      <div class="point-number point-number--dark">01</div>
      <p class="point-text">Lorem ipsum dolor sit amet, consectetur<br>adipisicing elit, sed do eiusmod tempor incididunt<br>ut labore et dolore magna aliqua.</p>
    </div>
    <div class="point point--2">
      <div class="point-number point-number--light">02</div>
      <p class="point-text">Lorem ipsum dolor sit amet, consectetur<br>adipisicing elit, sed do eiusmod tempor incididunt<br>ut labore et dolore magna aliqua.</p>
    </div>
    <div class="point point--3">
      <div class="point-number point-number--light">03</div>
      <p class="point-text">Lorem ipsum dolor sit amet, consectetur<br>adipisicing elit, sed do eiusmod tempor incididunt<br>ut labore et dolore magna aliqua.</p>
    </div>
    <div class="point point--4">
      <div class="point-number point-number--dark">04</div>
      <p class="point-text">Lorem ipsum dolor sit amet, consectetur<br>adipisicing elit, sed do eiusmod tempor incididunt<br>ut labore et dolore magna aliqua.</p>
    </div>

    <h2 class="summary-heading">SLIDE PRESENTATION</h2>
    <p class="summary-text">Lorem ipsum dolor sit amet, consectetur adipisicing elit, sed do eiusmod tempor incididunt ut labore et dolore magna aliqua. Ut enim ad minim<br>veniam. Lorem ipsum dolor sit amet, consectetur adipisicing elit, sed do eiusmod tempor incididunt ut labore et dolore magna aliqua.</p>
  </section>

  <section class="slide slide--model">
    <h1 class="slide-title"><span class="lead">GEMEINSAM KOMPETENZEN</span><span class="main">ENTWICKELN</span></h1>

    <div class="block block--left block--top">
      <h3 class="block-title">YOUR TITLE</h3>
      <p class="block-text">Lorem ipsum dolor sit amet,<br>consectetur adipisicing elit, sed do<br>eiusmod tempor incididunt.</p>
    </div>
    <div class="block block--right block--top">
      <h3 class="block-title">YOUR TITLE</h3>
      <p class="block-text">Lorem ipsum dolor sit amet,<br>consectetur adipisicing elit, sed do<br>eiusmod tempor incididunt.</p>
    </div>
    <div class="block block--left block--bottom">
      <h3 class="block-title">YOUR TITLE</h3>
      <p class="block-text">Lorem ipsum dolor sit amet,<br>consectetur adipisicing elit, sed do<br>eiusmod tempor incididunt.</p>
    </div>
    <div class="block block--right block--bottom">
      <h3 class="block-title">YOUR TITLE</h3>
      <p class="block-text">Lorem ipsum dolor sit amet,<br>consectetur adipisicing elit, sed do<br>eiusmod tempor incididunt.</p>
    </div>

    <svg class="model-graphic" viewBox="0 0 258 205" role="img" aria-label="Puzzle illustration: four blue puzzle pieces with small icons linked by outlined puzzle pieces">
      <defs>
        <linearGradient id="model-fill" x1="0" y1="0" x2="1" y2="1">
          <stop offset="0" stop-color="#1a5e91" stop-opacity="0.55"/>
          <stop offset="1" stop-color="#8eabc4" stop-opacity="0.55"/>
        </linearGradient>
      </defs>
      <rect x="0" y="0" width="258" height="205" fill="url(#model-fill)"/>
    </svg>
  </section>

</body>
</html>
```